Dental Medical History Form - Content provided

Design a medical history form for a dental practice. Content is provided so all that is needed is the formatting to make it look great and easy to read.

"Patient Information" to include all information contained in top portion of the "Patient Medical History Form" docx file.

"Medical History" should follow the formatting and content of the "Exact Medical History" file as this is what the entry fields look like in our practice software and so we would like it to match.

1st page - Patient info, allergies, medications, antibiotics, joint replacement, pregnancy.

2nd page - Do you have, or have you had, any of the following? . . . . . . .
Updates

Target Market(s)

All ages but must be clear enough for elderly to read. Use as much space as possible to keep font size bigger yet keep to two pages

Industry/Entity Type

Dental

Font styles to use
Sans Serif

Requirements
Must have
• All content provided
• Our logo at the top (file provided)
• Century Gothic Font
• Limit to two pages

```html
<!DOCTYPE html>
<html lang="en">
<head>
<meta charset="utf-8">
<title>Harbourline Dental – Confidential Medical History</title>
<link href="https://fonts.googleapis.com/css2?family=PT+Sans+Narrow:wght@400;700&display=swap" rel="stylesheet">
<style>
:root{
  --navy:#173f8c;
  --blue:#2160ad;
  --cyan:#86cde3;
  --field:#9fd4e8;
  --ink:#1b3b78;
  --paper:#ffffff;
  --backdrop:#e9eef5;
}
*{box-sizing:border-box;margin:0;padding:0}
html,body{width:1200px;height:784px;overflow:hidden}
body{background:var(--backdrop);font-family:"PT Sans Narrow",Arial Narrow,sans-serif;color:var(--ink);font-size:10px}
.form-page{position:absolute;left:330px;top:10px;width:540px;height:764px;background:var(--paper);box-shadow:0 2px 10px rgba(30,60,110,.18);padding:18px 24px 0 24px;overflow:hidden}
.page-edge{position:absolute;left:0;bottom:0;width:100%;height:10px;background:linear-gradient(90deg,var(--navy),var(--blue) 30%,var(--cyan) 60%,transparent 80%)}
.page-edge-left{position:absolute;left:0;bottom:0;width:10px;height:120px;background:linear-gradient(0deg,var(--navy),var(--cyan) 80%,transparent)}
.masthead{display:flex;justify-content:space-between;align-items:flex-start;height:58px}
.practice-name{display:flex;align-items:center;gap:8px;font-size:30px;font-weight:400;color:var(--ink);letter-spacing:.5px;line-height:1}
.practice-name .mark{width:12px;height:12px;border:1.5px solid var(--ink)}
.contact{text-align:right;font-weight:700;font-size:10px;line-height:1.25}
.contact .phone{display:flex;justify-content:flex-end;align-items:center;gap:5px;font-size:12px}
.title-band{position:relative;height:14px;margin:0 -24px 8px -24px;background:linear-gradient(90deg,var(--cyan) 0,var(--navy) 22%,var(--navy) 88%,var(--cyan) 100%)}
.title-band span{position:absolute;left:160px;top:1px;color:#fff;font-size:9px;letter-spacing:3px;font-weight:700}
.band{height:15px;margin:6px -24px 6px -24px;padding-left:30px;color:#fff;font-weight:700;font-style:italic;font-size:10px;line-height:15px;background:linear-gradient(90deg,var(--cyan) 0,var(--blue) 4%,var(--navy) 60%,var(--cyan) 100%)}
.row{display:flex;align-items:center;gap:6px;height:19px}
.label{white-space:nowrap}
.field{flex:1;height:14px;border:1px solid var(--field)}
.cap{white-space:nowrap;font-size:9px;margin-left:4px}
.box{display:inline-block;width:9px;height:9px;border:1px solid var(--field);vertical-align:middle;margin:0 5px 0 3px}
.options{display:flex;flex-wrap:wrap;row-gap:6px;padding:2px 0}
.options span{width:16.66%;white-space:nowrap}
.write-lines{display:grid;grid-template-columns:1fr 1fr;column-gap:20px;row-gap:13px;padding:6px 0 4px}
.write-lines i{display:block;border-bottom:1px solid var(--ink);height:1px}
.questions{margin-top:8px;line-height:22px}
.questions .row{height:22px}
.turnover{position:absolute;right:40px;bottom:22px;font-weight:700;font-style:italic;font-size:15px;color:var(--blue)}
</style>
</head>
<body>
<main class="form-page">
  <header class="masthead">
    <div class="practice-name"><span>harbourline dental</span><span class="mark"></span></div>
    <div class="contact">
      <div class="phone">
        <svg width="13" height="13" viewBox="0 0 14 14" aria-hidden="true"><rect width="14" height="14" rx="3" fill="#2f8fc4"/><path d="M4.5 3.2l1.4 2-.8 1a5 5 0 0 0 2.7 2.7l1-.8 2 1.4-.7 1.4c-3.4-.3-6.2-3.1-6.5-6.5z" fill="#fff"/></svg>
        <span>(02) 4310 5820</span>
      </div>
      <div>Harbourline Dental, 3.04/118 Lakeside Rd,</div>
      <div>Tern Bay NSW 2261</div>
    </div>
  </header>

  <div class="title-band"><span>CONFIDENTIAL MEDICAL HISTORY</span></div>

  <section class="patient">
    <div class="row"><span class="label">Name:</span><span class="field"></span><span class="cap">First</span><span class="field"></span><span class="cap">Middle</span><span class="field"></span><span class="cap">Last</span></div>
    <div class="row"><span class="label">Address:</span><span class="field"></span></div>
    <div class="row"><span class="label">DOB:</span><span class="field" style="flex:.6"></span><span class="label">Email Address:</span><span class="field"></span></div>
    <div class="row"><span class="label">Phone Number(s): Mobile</span><span class="field"></span><span class="label">Work</span><span class="field"></span><span class="label">Home</span><span class="field"></span></div>
    <div class="row"><span class="label">Emergency Contact Person: Name:</span><span class="field"></span><span class="label">Relationship:</span><span class="field" style="flex:.6"></span><span class="label">Phone number:</span><span class="field" style="flex:.7"></span></div>
  </section>

  <div class="band">General Practitioner:</div>
  <section class="practitioner">
    <div class="row"><span class="label">Name:</span><span class="field"></span></div>
    <div class="row"><span class="label">Practice Name:</span><span class="field"></span><span class="label">Phone Number:</span><span class="field" style="flex:.6"></span></div>
    <div class="row"><span class="label">Do you have a health fund with dental cover? Yes<span class="box"></span>or No<span class="box"></span>If so, what is the name of the fund?</span><span class="field"></span></div>
    <div class="row"><span class="label">Fund Number:</span><span class="field"></span><span class="label">Priority Number on card: 0<span class="box"></span>1<span class="box"></span>2<span class="box"></span>3<span class="box"></span>4<span class="box"></span>5<span class="box"></span></span></div>
    <div class="row"><span class="label">Occupation:</span><span class="field"></span></div>
    <div class="row"><span class="label">Referred by:</span><span class="field"></span></div>
  </section>

  <div class="band">Please indicate if you are allergic to any of the following(s)?</div>
  <section class="options allergies">
    <span>Aspirin<i class="box"></i></span><span>Codeine<i class="box"></i></span><span>Penicillin<i class="box"></i></span><span>Sulfites<i class="box"></i></span><span>Latex<i class="box"></i></span><span>Lactose<i class="box"></i></span>
    <span>Local Anaesthetic<i class="box"></i></span><span>Nickel<i class="box"></i></span>
  </section>
  <div class="row"><span class="label">Other:</span><span class="field"></span></div>

  <div class="band">Are you currently taking, or have ever taken, any of the following medications?</div>
  <section class="options medications">
    <span>Asthma Inhaler<i class="box"></i></span><span>Anti-epileptics<i class="box"></i></span><span>Anti-depressants<i class="box"></i></span><span>Blood Pressure<i class="box"></i></span><span>Blood Thinners<i class="box"></i></span><span>Bisphosphonates<i class="box"></i></span>
    <span>Chemotherapy<i class="box"></i></span><span>Insulin<i class="box"></i></span><span>Immunosuppressants<i class="box"></i></span><span>Steroids<i class="box"></i></span><span>Oral Contraceptive<i class="box"></i></span><span>Other<i class="box"></i></span>
  </section>

  <div class="band">Please specify medication name, dose, and frequency where possible:</div>
  <section class="write-lines">
    <i></i><i></i><i></i><i></i><i></i><i></i><i></i><i></i>
  </section>

  <section class="questions">
    <div class="row"><span class="label">Do you require antibiotic cover?</span><span class="label" style="margin-left:30px">Yes<span class="box"></span>No<span class="box"></span></span></div>
    <div class="row"><span class="label">Have you had a joint replacement?</span><span class="label" style="margin-left:20px">Yes<span class="box"></span>No<span class="box"></span></span></div>
    <div class="row"><span class="label">Women: Are you pregnant?</span><span class="label" style="margin-left:20px">Yes<span class="box"></span>No<span class="box"></span>Possible<span class="box"></span>or</span><span class="label" style="margin-left:20px">Breast Feeding?</span><span class="label" style="margin-left:20px">Yes<span class="box"></span>No<span class="box"></span></span></div>
  </section>

  <div class="turnover">Please Turnover</div>
  <div class="page-edge"></div>
  <div class="page-edge-left"></div>
</main>
</body>
</html>
```